Webdesign für Brenner Werkstatt
Zielgruppe
Brenner Werkstatt produziert GfK Formteile und Abdeckungen
Einzelanfertigungen • Negativ - Formenbau • Prototyping • Ur-Modellbau
Formteile • Abdeckungen • Behälter • Sonderanfertigungen • Beschichtungen
Prototypen Modellbau • Anfertigung von Negativformen • Reparaturen • Fahrzeugteile
Hauptzielgruppe ist die Luftfahrtindustrie (Abdeckungen für Triebwerke)
Durch den Prototypenbau und die Einzelanfertigungen ist die Zielgruppe nicht klar zu definieren. Es werden Einzelteile jeglicher Art aus GfK hergestellt.
Dies können auch Anbauteile für PKW, Poolbeschichtungen, Teile für Boote etc sein.
Es gibt auch Kleinserien. Beispielsweise baut Brenner-Werkstatt Motorhauben für Karl-Honstett Rasenmähertrecker aus den 70er Jahren nach, die es nicht mehr zu kaufen gibt.
Aufgabenstellung
Der Designer hat alle Freiheiten. Die Seite muss natürlich responsiv funktionieren.
Außer dem Logo gibt es keine must-haves.
Schriftart aus dem Logo: EXO 2

```html
<!DOCTYPE html>
<html lang="de">
<head>
<meta charset="utf-8">
<title>Brenner Werkstatt – Formbauteile</title>
<link rel="stylesheet" href="https://fonts.googleapis.com/css2?family=Exo+2:wght@300;400;500;700;800&display=swap">
<style>
  :root {
    --blue: #1b5e9b;
    --blue-dark: #134b80;
    --blue-line: #8fb0cf;
    --text: #1e1e1e;
    --gray-band: #f0f0f0;
    --white: #ffffff;
  }
  * { box-sizing: border-box; margin: 0; padding: 0; }
  html, body { width: 1200px; height: 3070px; overflow: hidden; }
  body {
    position: relative;
    background: var(--white);
    font-family: "Exo 2", sans-serif;
    color: var(--text);
  }
  .abs { position: absolute; }

  /* Header */
  .meta-links { top: 18px; left: 899px; display: flex; gap: 24px; font-size: 15px; color: var(--blue); }
  .flag { top: 17px; left: 1055px; width: 35px; height: 22px; }
  .brand-mark { top: 62px; left: 250px; width: 46px; height: 46px; background: var(--blue); }
  .brand-name { top: 56px; left: 322px; font-size: 58px; font-weight: 800; color: var(--blue); letter-spacing: -1px; line-height: 1.2; }
  .brand-tag { top: 143px; left: 322px; font-size: 19px; color: #555; }

  .main-nav { top: 180px; left: 0; width: 1200px; height: 51px; background: var(--blue); }
  .main-nav ul { list-style: none; display: flex; height: 100%; padding-left: 298px; }
  .main-nav li { position: relative; height: 100%; display: flex; align-items: center; padding: 0 25px; color: var(--white); font-size: 17px; border-right: 1px solid rgba(255,255,255,.12); }
  .main-nav li:last-child { border-right: none; }
  .main-nav li.is-active { background: var(--blue-dark); }
  .main-nav li.is-active::after { content: ""; position: absolute; bottom: -8px; left: 50%; margin-left: -8px; border: 8px solid transparent; border-bottom: 0; border-top-color: var(--blue-dark); }

  /* Hero */
  .hero { top: 231px; left: 0; width: 1200px; height: 492px; background: linear-gradient(110deg, #6b5a48 0%, #2f5fc4 18%, #2e55b8 45%, #3b67cf 60%, #b9a36a 75%, #2c58c0 88%, #7a6a58 100%); }
  .hero-title { top: 267px; left: 808px; width: 392px; height: 112px; background: rgba(255,255,255,.85); padding: 18px 0 0 30px; font-size: 31px; font-weight: 800; color: var(--blue); }

  /* Sidebar */
  .side-head { top: 794px; left: 0; width: 399px; height: 41px; background: var(--blue); color: var(--white); font-weight: 700; font-size: 17px; text-align: right; padding: 9px 17px 0 0; }
  .side-nav { top: 848px; left: 110px; width: 288px; list-style: none; }
  .side-nav li { height: 37px; margin-bottom: 1px; border-bottom: 1px solid var(--blue-line); display: flex; align-items: center; justify-content: center; font-size: 15px; color: var(--blue); }
  .side-nav li:last-child { border-bottom: none; }
  .side-nav li.is-active { background: var(--blue); color: var(--white); }

  /* Content */
  .lead { top: 803px; left: 457px; width: 636px; text-align: center; font-size: 24px; font-weight: 300; line-height: 30px; }
  .copy { top: 959px; left: 457px; width: 636px; font-size: 16.5px; font-weight: 300; line-height: 21px; }
  .copy p { margin-bottom: 21px; }

  /* Gallery */
  .gallery-band { top: 1382px; left: 0; width: 1200px; height: 1220px; background: var(--gray-band); }
  .tile { width: 288px; height: 295px; box-shadow: 0 4px 6px rgba(0,0,0,.18); }
  .t1 { top: 1449px; left: 110px; background: linear-gradient(160deg, #cfd3d8, #1f4fa3 50%, #2a2a3a); }
  .t2 { top: 1449px; left: 457px; background: linear-gradient(160deg, #4a4a4a, #e8772b 45%, #3f3f3f); }
  .t3 { top: 1449px; left: 805px; background: linear-gradient(170deg, #b9a48a, #e4e2da 50%, #c9b08a); }
  .t4 { top: 1801px; left: 110px; background: linear-gradient(160deg, #8f8f8f, #d2d0cc 50%, #5b5b5b); }
  .t5 { top: 1801px; left: 457px; background: linear-gradient(120deg, #d9d4c8, #b5532a 45%, #ededeb); }
  .t6 { top: 1801px; left: 805px; background: linear-gradient(160deg, #a69d8a, #ece6d4 50%, #3a3a3a); }
  .t7 { top: 2157px; left: 110px; background: linear-gradient(120deg, #c8c8c6, #e9e6dc 50%, #a09a8c); }

  /* Footer */
  .contact-tab { top: 2558px; left: 92px; width: 204px; height: 45px; }
  .contact-tab span { position: absolute; left: 48px; top: 2px; font-size: 31px; font-weight: 800; color: var(--white); }
  .footer { top: 2602px; left: 2px; width: 1198px; height: 468px; background: var(--blue); color: var(--white); }
  .footer-brand { top: 2647px; left: 140px; font-size: 29px; font-weight: 700; color: var(--white); }
  .footer-address { top: 2694px; left: 140px; font-size: 19px; font-weight: 700; line-height: 24px; color: var(--white); }
  .footer-phone { top: 2789px; left: 140px; font-size: 19px; font-weight: 700; line-height: 24px; color: var(--white); }
  .footer-phone span { display: inline-block; width: 60px; }
  .form-title { top: 2650px; left: 663px; font-size: 27px; font-weight: 700; color: var(--white); }
  .field { left: 643px; width: 447px; background: var(--white); border: 1px solid #0e3e6a; box-shadow: inset 0 -2px 0 #0e3e6a; color: var(--blue); font-size: 20px; padding: 7px 0 0 20px; }
  .f-name { top: 2689px; height: 41px; }
  .f-mail { top: 2749px; height: 41px; }
  .f-msg { top: 2810px; height: 143px; padding-top: 12px; }
  .send { top: 2968px; left: 971px; width: 121px; height: 38px; background: var(--blue-dark); color: var(--white); font-weight: 700; font-size: 19px; display: flex; align-items: center; justify-content: center; letter-spacing: .5px; }
</style>
</head>
<body>
  <header>
    <nav class="meta-links abs"><span>Impressum</span><span>AGB</span></nav>
    <svg class="flag abs" viewBox="0 0 35 22" aria-label="Deutsch">
      <rect width="35" height="22" fill="#e8e8e8"/>
      <rect x="3" y="3" width="29" height="5.3" fill="#000"/>
      <rect x="3" y="8.3" width="29" height="5.3" fill="#dd0000"/>
      <rect x="3" y="13.6" width="29" height="5.4" fill="#ffce00"/>
    </svg>
    <div class="brand-mark abs"></div>
    <div class="brand-name abs">Brenner Werkstatt</div>
    <div class="brand-tag abs">GfK Formteile | Ur-Modellbau | Prototyping</div>
    <nav class="main-nav abs">
      <ul>
        <li>Startseite</li>
        <li>Über uns</li>
        <li class="is-active">Produkte &amp; Dienstleistungen</li>
        <li>Kontakt</li>
      </ul>
    </nav>
  </header>

  <div class="hero abs" role="img" aria-label="Foto: blaue GfK-Formbauteile in der Werkstatt"></div>
  <h1 class="hero-title abs">Formbauteile</h1>

  <aside>
    <div class="side-head abs">Produkte &amp; Dienstleistungen</div>
    <ul class="side-nav abs">
      <li>Luftfahrt Formbauteile</li>
      <li>Aufblasbare Sonderabdeckungen</li>
      <li class="is-active">Formbauteile</li>
      <li>Ur-Modellbau</li>
      <li>Aquarienrückwände</li>
      <li>Dekoration &amp; Kunstfelsen</li>
      <li>Fahrzeugteile</li>
      <li>Prototypen Metallbau</li>
      <li>Reparaturen</li>
    </ul>
  </aside>

  <main>
    <p class="lead abs">Wir bieten Ihnen die Anfertigung von<br>technischen Formbauteilen in Einzelstück-<br>oder Kleinserienfertigung an.</p>
    <div class="copy abs">
      <p>Der Modellbau nach Zeichnungen / Modell und die Anfertigung von Negativformen gehört ebenfalls zu unserem Leistungsangebot.</p>
      <p>Neben der Neuanfertigung bieten wir auch die Reparatur schon vorhandener Formbau-teile und Negativformen an.</p>
      <p>Im Rahmen unseres "Vor-Ort-Service" führen wir Reparaturarbeiten auch bei Ihnen direkt durch.</p>
      <p>Die abbgebildeten Bilder zeigen einige der von uns angefertigten Bauteile und Modelle für:</p>
      <p>• Fahrzeuginnenverkleidungen<br>• Behälterbau nach Maß<br>• Abdeckungen / Abtrennungen</p>
    </div>
  </main>

  <section>
    <div class="gallery-band abs"></div>
    <div class="tile t1 abs" role="img" aria-label="Foto: blaues zylindrisches Formbauteil"></div>
    <div class="tile t2 abs" role="img" aria-label="Foto: große orangefarbene Dekorationsfigur"></div>
    <div class="tile t3 abs" role="img" aria-label="Foto: helle Abdeckung auf Holzböcken"></div>
    <div class="tile t4 abs" role="img" aria-label="Foto: Fahrzeuginnenverkleidung als Rohteil"></div>
    <div class="tile t5 abs" role="img" aria-label="Foto: braune Negativform mit Formteil"></div>
    <div class="tile t6 abs" role="img" aria-label="Foto: GfK-Rohteile auf dem Werkstattboden"></div>
    <div class="tile t7 abs" role="img" aria-label="Foto: gebogene helle Formteile"></div>
  </section>

  <footer>
    <svg class="contact-tab abs" viewBox="0 0 204 45" aria-hidden="true">
      <polygon points="14,0 204,0 204,45 0,45" fill="var(--blue)"/>
      <polygon points="14,0 22,0 8,45 0,45" fill="var(--blue-dark)"/>
    </svg>
    <div class="contact-tab abs"><span>Kontakt</span></div>
    <div class="footer abs"></div>
    <div class="footer-brand abs">Brenner Werkstatt</div>
    <div class="footer-address abs">Geschäftsführer: M. Albrecht<br>Lindenhof-Str. 14<br>31582 Nordhain</div>
    <div class="footer-phone abs"><span>Tel.</span>+49 511 / 470 12 30<br><span>Fax.</span>+49 511 / 470 12 31</div>
    <div class="form-title abs">Ihre Nachricht</div>
    <div class="field f-name abs">Name</div>
    <div class="field f-mail abs">E-Mail</div>
    <div class="field f-msg abs">Nachricht</div>
    <div class="send abs">SENDEN</div>
  </footer>
</body>
</html>
```